Internationally renowned speaker/campaigner needs a book cover

I need a preliminary cover design for my new book "HALF-LANTERN".

I'm a medical doctor and an internationally renowned speaker and campaigner for human-centered and compassionate healthcare, co-founder of an international social movement PETALS in MEDICINE (http://petalsinmedicine-example.com), and successful author of the book 'ROOM TO LISTEN - Ways to cherish your clients and your work' (http://www.shopvantra-example.com/ROOM-LISTEN-cherish-your-clients/dp/9082614530)

The subtitle of HALF-LANTERN is: "How our one-eyed materialistic science leads to inequality, greed, poverty, violence, ill-health and environmental destruction (and what we can do about it)"

Author: Dr GARETH PELLWICK

Preliminary book blurb:
"As social activists and environmental campaigners we are continuously sabotaging our cause because our strategies are unconsciously supporting the materialistic foundations of our broken world.

Our materialistic science sees the natural world and even people as innate objects, without consciousness or connection. Modern medicine treats patients as broken machines to be fixed, not as conscious, subjective beings. And economic theory says every person is an independent agent, striving to maximize advantage. We turn every human and natural gift into a commodity to be owned, controlled, bought and sold.

Our social policies, education system, justice system and even our democracy assume that incentives, rewards and punishments are the ‘real’ motives for human behavior. Our purpose in life is to ‘get ahead’ and accumulate material goods. Therein lies competition, insecurity, greed, violence, ill-health and the destruction of the natural environment.

Materialistic science is simply blind to the life-world of consciousness, intelligence, purpose and deep interdependence in all natural and human systems. We all know that compassion, kindness, love, and human creativity are the real foundation of our communities, not mindless competition.

But so immersed are we in materialistic assumptions, that in our campaigns we mistakenly adopt tools and strategies from the existing system in our struggle for a better world. But the moment we fight against anything, or demonize our opposition, or sell our ideas for money, or charitably impose our solutions, we only strengthen the material world.

Instead, we have to be the change we want to see: grow an economy of generosity and gifting, freely share ideas, focus on solutions not problems, and deeply believe in the capacity for creativity and healing in every person and every community. You can download this book for free at halflantern-example.org."

Design brief
I need a compelling front page image and title design that conveys the idea that our science is one-eyed or half-blind, hence the title name 'half-lantern', which means half-science.

Our predominant science only sees the material world, not the conscious world. We need both.

I'm also preparing a QUORx talk on the subject and want the compelling image and title to use for this purpose also.

The genre of books is in the class of leadership, entrepreneurs, positive psychology, community development - and I have uploaded some cover images of books in this class. The cover of my current book, ROOM TO LISTEN, has elements of the style I'm looking for: bold, bright, simple, metaphorical, a surprising juxtaposition of technical and human.

The way I develop and market the book will be congruent with the ideas expressed. I will give the e-book away for free and invite people to make a donation if they like it (gift economy). The book will be published on the website unfinished, inviting comments, suggestions, stories and ideas to be included in the finished book. So to a degree, the content of the book will be fully developed by crowdsourcing living examples of the core ideas and creating a community of conversation (including a Chatterbay page). I'll later be looking for a simple WordPress website design based on the book cover graphic, fonts and colours.

So this first design brief and contract is for an e-book cover and later the book will be self-published as a paperback using PressNook.

Target Market(s)

The target audience is readers who are community leaders and social activists - all those utterly passionate about creating a better world, whether it's in the environment, education, healthcare, violence prevention, justice, health communities, etc.

Requirements
Must have
• A compelling image that symbolises the key idea - eyecatching
Should not have
• Must not express 'corporate' concepts, power or hierarchy

```html
<!DOCTYPE html>
<html lang="en">
<head>
<meta charset="utf-8">
<title>HALF-LANTERN — Dr Gareth Pellwick</title>
<link rel="stylesheet" href="https://fonts.googleapis.com/css2?family=League+Gothic&family=Montserrat:wght@600;800&family=Oswald:wght@300&display=swap">
<style>
  :root {
    --cover-red: #d4161e;
    --ink: #1e1414;
    --paper: #ffffff;
    --band-grey: #58585a;
    --band-orange: #f39422;
    --band-red: #dc1f26;
    --band-blue: #3b8ccb;
    --band-green: #12783c;
  }
  html, body {
    margin: 0;
    padding: 0;
    overflow: hidden;
    background: var(--paper);
  }
  .cover {
    position: relative;
    width: 750px;
    height: 1200px;
    background: var(--paper);
    overflow: hidden;
  }
  .cover-title {
    position: absolute;
    left: 0;
    top: 92px;
    width: 750px;
    margin: 0;
    text-align: center;
    font-family: "Montserrat", sans-serif;
    font-weight: 800;
    font-size: 74px;
    line-height: 96px;
    letter-spacing: -1px;
    color: var(--cover-red);
    white-space: nowrap;
  }
  .subtitle {
    position: absolute;
    left: 0;
    top: 250px;
    width: 750px;
    margin: 0;
    text-align: center;
    font-family: "Montserrat", sans-serif;
    font-weight: 600;
    color: var(--ink);
    font-size: 25px;
    line-height: 32px;
    letter-spacing: -0.5px;
    white-space: nowrap;
  }
  .subtitle .subtitle-caps {
    display: block;
    font-size: 24.5px;
  }
  .tagline {
    position: absolute;
    left: 0;
    top: 352px;
    width: 750px;
    margin: 0;
    text-align: center;
    font-family: "Oswald", sans-serif;
    font-weight: 300;
    font-size: 44px;
    letter-spacing: 6px;
    color: var(--cover-red);
    line-height: 56px;
  }
  .cover-art {
    position: absolute;
    left: 144px;
    top: 488px;
    width: 452px;
    height: 572px;
    background: linear-gradient(
      to bottom,
      var(--band-grey) 0%,
      var(--band-grey) 30%,
      var(--band-orange) 34%,
      var(--band-orange) 50%,
      var(--band-red) 54%,
      var(--band-red) 74%,
      var(--band-blue) 78%,
      var(--band-blue) 93%,
      var(--band-green) 96%
    );
    border-radius: 48% 46% 8% 8% / 30% 30% 4% 4%;
  }
  .author-band {
    position: absolute;
    left: 0;
    top: 1060px;
    width: 750px;
    height: 140px;
    background: var(--cover-red);
  }
  .author-name {
    position: absolute;
    left: 118px;
    top: 12px;
    width: 516px;
    height: 114px;
    display: block;
  }
  .author-name text {
    font-family: "League Gothic", "Oswald", sans-serif;
    fill: var(--paper);
  }
</style>
</head>
<body>
  <main class="cover">
    <h1 class="cover-title">HALF-LANTERN</h1>

    <p class="subtitle">
      How our one-eyed materialistic science leads to
      <span class="subtitle-caps">INEQUALITY, GREED, POVERTY, VIOLENCE,</span>
      <span class="subtitle-caps">ILL-HEALTH AND ENVIRONMENTAL DESTRUCTION</span>
    </p>

    <p class="tagline">and what we can do about it</p>

    <div class="cover-art" role="img" aria-label="Illustration: profile silhouette of a head split into torn coloured bands of grey, orange, red, blue and green, filled with molecule models, chemical formulas and a laboratory flask"></div>

    <footer class="author-band">
      <svg class="author-name" viewBox="0 0 516 114" aria-label="Dr GARETH PELLWICK">
        <text x="0" y="110" font-size="146" textLength="516" lengthAdjust="spacingAndGlyphs">Dr GARETH PELLWICK</text>
      </svg>
    </footer>
  </main>
</body>
</html>
```